Consulting Practice for Charities Needs A Brochure Deisgn

Hi! We need a tri-fold brochure for a Washington, DC based consulting practice that works with charities (NGOs, Associations, etc.) and wealthy donors (philanthropists). Our company, Morrow Civic Advisors, helps nonprofits to implement practices that maximize organizational efficiency and effectiveness - by working directly with board members and staff.
Our clients are well educated and quite sophisticated (some charities are international with multi-million dollar budgets, while others are quite local and small) This brochure will be handed to them by some of our 'referral partners' (law firms, accountants and even governmental agencies) in addition to being given out during our presentations. We draw inspiration from nature and would like to somehow include a "natural / eco-friendly" feel to the piece, including natural colors .... that being said, not in any way "folksy" - it must be sophisticated.

Target Market(s)

nonprofit executive directors, board chairs, wealth holders (philanthropists)

Industry/Entity Type

Consulting

Requirements
Must have
• I uploaded a word file with content (text) - most of that needs to be on the brochure ... but ... if it looks too crowded, let me know and I'll reduce
Nice to have
• pop-out quotes (maybe from testimonials??), nature - theme of some kind but also photo of boardroom (links to samples are like are uploaded in a word doc below)
Should not have
• nothing cute ... nothing too feminine

```html
<!DOCTYPE html>
<html lang="en">
<head>
<meta charset="utf-8">
<title>Morrow Civic Advisors – Tri-fold Brochure</title>
<link rel="stylesheet" href="https://fonts.googleapis.com/css2?family=Roboto+Slab:wght@300;400;700&display=swap">
<style>
  :root{
    --bg:#d2d3d5;
    --paper:#ffffff;
    --purple:#7b72b6;
    --purple-dark:#5d5590;
    --orange:#f39325;
    --grey:#8e8e92;
    --ink:#3c3c3e;
    --muted:#6a6a6e;
  }
  *{box-sizing:border-box;margin:0;padding:0}
  html,body{width:1200px;height:970px;overflow:hidden;background:var(--bg)}
  body{font-family:"Roboto Slab",Georgia,serif;color:var(--ink)}
  .brochure{position:absolute;left:67px;top:72px;width:1073px;height:832px;background:var(--paper);box-shadow:0 1px 3px rgba(0,0,0,.15)}
  .panel{position:absolute;top:0;width:358px;height:784px;overflow:hidden}
  .panel--left{left:0;background:linear-gradient(90deg,#fff 85%,#f3f3f3)}
  .panel--middle{left:358px;background:linear-gradient(90deg,#f2f2f2,#fafafa 12%,#fafafa 88%,#f2f2f2)}
  .panel--right{left:716px;width:357px;background:linear-gradient(90deg,#f3f3f3,#fff 15%)}
  .photo{position:absolute;left:0;top:0;display:block}

  /* Left panel */
  .section-title{font-weight:700;color:var(--purple);font-size:21px;letter-spacing:.2px}
  .who{position:absolute;left:32px;top:256px;width:300px}
  .who p{font-size:12.4px;font-weight:300;line-height:15.9px;margin-top:8px}
  .who p + p{margin-top:15px}
  .steps{position:absolute;left:31px;top:491px;height:40px;width:295px}
  .steps svg{position:absolute;left:0;top:0}
  .steps span{position:absolute;top:5px;color:#fff;font-size:12.4px;line-height:14.5px;font-weight:400;white-space:nowrap}
  .will{position:absolute;left:33px;top:544px;width:300px}
  .will h3{font-size:12.6px;font-weight:400;color:var(--purple)}
  .will ul{list-style:none;margin-top:12px}
  .will li{position:relative;padding-left:22px;font-size:12.4px;font-weight:300;line-height:13px;margin-bottom:13px}
  .will li::before{content:"";position:absolute;left:8px;top:5px;width:4px;height:4px;border-radius:50%;background:#9a9a9a}

  /* Middle panel */
  .quote{position:absolute;left:40px;top:85px;width:282px;height:150px;background:var(--grey);color:#fff;text-align:center;padding:31px 18px 0;font-size:11.6px;line-height:16px;font-weight:300}
  .quote strong{font-weight:700;display:block}
  .quote-mark{position:absolute;left:157px;top:60px;width:48px;height:48px;border-radius:50%;background:#fff;border:2px solid var(--purple);color:var(--grey);font-size:40px;font-weight:700;text-align:center;line-height:56px}
  .certs-title{position:absolute;left:0;width:358px;top:270px;text-align:center}
  .badge{position:absolute;display:block}
  .codes{position:absolute;left:299px;top:369px;font-size:8px;line-height:10px;font-weight:300}
  .contact{position:absolute;left:0;top:449px;width:358px;height:335px}
  .contact-info{position:absolute;left:0;top:0;width:358px;text-align:center;color:#fff}
  .brand-name{font-weight:400;font-size:21px;line-height:24px;letter-spacing:.3px}
  .contact-info .brand-name{position:absolute;left:0;width:358px;top:72px}
  .icon-circle{position:absolute;left:164px;width:30px;height:30px;border:1.5px solid #fff;border-radius:50%}
  .phone{position:absolute;left:0;width:358px;top:156px;font-size:20px;font-weight:300;letter-spacing:.5px}
  .web{position:absolute;left:0;width:358px;top:190px;font-size:13px;line-height:17px;font-weight:400}
  .social{position:absolute;left:0;width:358px;top:270px;font-size:13px;font-weight:400}

  /* Right panel */
  .brand{position:absolute;left:0;width:357px;top:538px;text-align:center}
  .brand .brand-name{color:var(--purple);font-size:24px}
  .brand i{display:inline-block;width:10px;height:10px;background:var(--purple);margin-right:8px;vertical-align:2px}
  .tagline{position:absolute;left:0;width:357px;top:637px;text-align:center;color:var(--orange);font-weight:700;font-size:21px;line-height:26px}
  .lede{position:absolute;left:18px;width:321px;top:707px;text-align:center;font-size:12.4px;line-height:16px;font-weight:300}

  /* Footer */
  .footer{position:absolute;left:0;top:784px;width:1073px;height:48px;border-top:5px solid var(--orange);background:var(--purple);display:flex}
  .footer span{flex:1;text-align:center;color:#fff;font-size:13.4px;font-weight:400;line-height:43px}
</style>
</head>
<body>
<div class="brochure">

  <section class="panel panel--left">
    <svg class="photo" width="358" height="250" viewBox="0 0 358 250" role="img" aria-label="Photo of a team of consultants meeting around a boardroom table">
      <defs>
        <linearGradient id="boardroom" x1="0" y1="0" x2="0" y2="1">
          <stop offset="0" stop-color="#b9d3da"/>
          <stop offset=".45" stop-color="#7f8e99"/>
          <stop offset="1" stop-color="#2f3440"/>
        </linearGradient>
      </defs>
      <path d="M0 0H358V190Q300 262 170 236Q80 222 0 200Z" fill="url(#boardroom)"/>
      <path d="M8 220Q120 246 230 232Q320 218 358 178L358 198Q320 240 230 244Q120 250 8 224Z" fill="var(--purple)"/>
    </svg>

    <div class="who">
      <h2 class="section-title">Who We Are:</h2>
      <p>Founded in 2010 by Helen Marie Corbin Morrow, MCA was inspired by the national climate for stronger governance and deeper board engagement. Since then, we’ve worked with hundreds of board members to improve the impact of their philanthropic efforts.</p>
      <p>Our energetic and patient team of experts in nonprofit governance, operations and management will provide a comprehensive approach to problem solving, training and coaching. The result?</p>
    </div>

    <div class="steps">
      <svg width="295" height="40" viewBox="0 0 295 40" aria-hidden="true">
        <path d="M3 0H80L95 20L80 40H3Q0 40 0 37V3Q0 0 3 0Z" fill="var(--orange)"/>
        <path d="M84 0H203L218 20L203 40H84L99 20Z" fill="var(--grey)"/>
        <path d="M207 0H280L295 20L280 40H207L222 20Z" fill="var(--orange)"/>
      </svg>
      <span style="left:14px">Better<br>Boards</span>
      <span style="left:109px">Stronger<br>Organizations</span>
      <span style="left:229px">Greater<br>Impact</span>
    </div>

    <div class="will">
      <h3>MCA consultants will:</h3>
      <ul>
        <li>Bring new perspectives and skills for strategic or generative (big picture) thinking</li>
        <li>Challenge your assumptions</li>
        <li>Offer innovative approaches to problem solving</li>
        <li>Identify sources of dysfunction</li>
        <li>Devise tactics to improve decision making or communication</li>
        <li>Make breakthrough improvements</li>
      </ul>
    </div>
  </section>

  <section class="panel panel--middle">
    <blockquote class="quote">
      <strong>Dana Whitfield (CEO, Capital Shelter Alliance)</strong>
      “I would recommend Helen without reservation. Her Governance Council training and her knowledge of both Board dynamics and the needs of donors is uniquely helpful.”
    </blockquote>
    <div class="quote-mark" aria-hidden="true">“</div>

    <h2 class="section-title certs-title">Certificates:</h2>
    <svg class="badge" style="left:32px;top:318px" width="82" height="62" viewBox="0 0 82 62" role="img" aria-label="Governance trainer certification badge"><rect width="82" height="62" rx="4" fill="#2b6fa5"/></svg>
    <svg class="badge" style="left:130px;top:312px" width="120" height="68" viewBox="0 0 120 68" role="img" aria-label="Women-owned small business certification badge"><rect width="120" height="68" rx="4" fill="#2d2d2f"/></svg>
    <svg class="badge" style="left:257px;top:315px" width="50" height="50" viewBox="0 0 50 50" role="img" aria-label="Industry classification listing badge"><circle cx="25" cy="25" r="25" fill="#1b5ea8"/></svg>
    <div class="codes">541611<br>561990<br>611430</div>

    <div class="contact">
      <svg class="photo" width="358" height="335" viewBox="0 0 358 335" role="img" aria-label="Photo of a calm forest lake with reeds at dusk">
        <defs>
          <linearGradient id="lake" x1="0" y1="0" x2="0" y2="1">
            <stop offset="0" stop-color="#5e6f64"/>
            <stop offset=".3" stop-color="#3e4a45"/>
            <stop offset=".55" stop-color="#6f6a8f"/>
            <stop offset="1" stop-color="#3d3767"/>
          </linearGradient>
        </defs>
        <path d="M0 20Q150 -6 358 14V335H0Z" fill="url(#lake)"/>
        <path d="M0 18Q120 -20 320 18Q160 -4 0 30Z" fill="var(--orange)"/>
      </svg>
      <div class="contact-info">
        <div class="brand-name">Morrow Civic Advisors</div>
        <span class="icon-circle" style="top:120px">
          <svg width="27" height="27" viewBox="0 0 27 27" aria-hidden="true"><path d="M9 8c-1 1-1 3 1 6s5 5 7 5l2-2-3-2-1 1c-1 0-3-2-3-3l1-1-2-3z" fill="none" stroke="#fff" stroke-width="1.3" stroke-linejoin="round"/></svg>
        </span>
        <div class="phone">+1.202.555.0148</div>
        <div class="web">info@morrowcivicadvisors.com<br>MorrowCivicAdvisors.com</div>
        <span class="icon-circle" style="top:238px"></span>
        <div class="social">in/morrowcivicadvisors</div>
      </div>
    </div>
  </section>

  <section class="panel panel--right">
    <svg class="photo" width="357" height="495" viewBox="0 0 357 495" role="img" aria-label="Photo of a marsh and pond edged by tall evergreen trees">
      <defs>
        <linearGradient id="marsh" x1="0" y1="0" x2="0" y2="1">
          <stop offset="0" stop-color="#8a929a"/>
          <stop offset=".3" stop-color="#3f5a3a"/>
          <stop offset=".62" stop-color="#7f8f4c"/>
          <stop offset="1" stop-color="#4f5230"/>
        </linearGradient>
      </defs>
      <path d="M0 0H357V410Q330 470 230 480Q140 486 0 458Z" fill="url(#marsh)"/>
      <path d="M0 458Q140 486 230 476Q330 466 357 400V420Q330 484 230 488Q140 494 0 464Z" fill="var(--purple)"/>
    </svg>
    <div class="brand"><span class="brand-name"><i></i>Morrow Civic Advisors</span></div>
    <h2 class="tagline">Changing the culture<br>of philanthropy</h2>
    <p class="lede">We help nonprofit clients excel by implementing exceptional governance practices.<br>We counsel private clients on involvement with sound philanthropic enterprises.</p>
  </section>

  <footer class="footer">
    <span>MorrowCivicAdvisors.com</span>
    <span>MorrowCivicAdvisors.com</span>
    <span>MorrowCivicAdvisors.com</span>
  </footer>
</div>
</body>
</html>
```